wardrobe/costume stylist needs good business card for own business

Hi:)

I'm wanting a business card for my company. I am a freelance stylist.

I do wardrobe/costume stylist to TV commercials; Films; Fashion and Lifestyle shoots.

I'd like a design based around my name Rosalind Parfrey written nicely, maybe a colour? Up to you?!

I've attached a couple of images of business cards I like
.... be creative and have fun!

Thank you :)

Reason: I was trying to get my new business card ready for before I headed overseas Friday morning but I don't think that was realistic so I'd like to extend the deadline to give time to the project. Thank you

Hi designers:) Thank you for all your designs, I've extended the deadline until Sunday, so there's a bit more time. I've attached 3 pictures of business cards which I quite like, please take a look to see if it can be of help in your process. I like the pale plain or patterned background with dark font and the dark plain or patterned background with the pale font the motifs the feminine fonts the plain fonts I like the idea of playing with a circle or some shape on one side of the card with my name or initials as in the picture I have on my post could you play around with this idea a bit please? Thank you all for the work you've done :) Rosa

Hi I am working overseas til Saturday night sorry for no feedback until I teturn Thanks :) Rosa

Hi designers, Thank you all so much for submitting your designs, I really appreciate your input into my project :) I'm sorry I didn't get to respond to some comments, and give feedback. I didn't back from being away until later than I expected, and the deadline had passed then, so apologies. Thanks to you all again for all your really good designs :) Rosa

Target Market(s)

I am a freelance stylist my target audience is producers, production companies, photographers, directors...

Industry/Entity Type

Business

Requirements
Must have
• Rosalind Parfrey
Stylist or Wardrobe Stylist

email rosaparfrey@mailbox-example.co.nz
Mobile 0218467193

(Don't have to use the words 'email' and 'mobile')
Nice to have
• Would like it to be double sided
Like B & W
Like pale colour background with dark font or white font
Like dark colour background with pale font
Should not have
• I would prefer it not to incorporate pictures

```html
<!DOCTYPE html>
<html lang="en">
<head>
<meta charset="utf-8">
<title>Rosalind Parfrey — Stylist business card</title>
<link rel="stylesheet" href="https://fonts.googleapis.com/css2?family=Roboto:wght@300;400;700&display=swap">
<style>
  :root {
    --paper: #ffffff;
    --ink: #000000;
    --card-edge: #d9d9d9;
    --back-ink: #ffffff;
  }
  * { margin: 0; padding: 0; box-sizing: border-box; }
  html, body {
    width: 1200px;
    height: 1200px;
    overflow: hidden;
    background: var(--paper);
    font-family: "Roboto", Arial, sans-serif;
  }
  .spread {
    position: absolute;
    left: 131px;
    top: 462px;
    width: 939px;
    height: 276px;
    display: flex;
  }
  .card {
    width: 469.5px;
    height: 276px;
    position: relative;
  }
  .card--front {
    background: var(--paper);
    border: 1px solid var(--card-edge);
    border-right: none;
  }
  .card--back {
    background: var(--ink);
    color: var(--back-ink);
  }
  .wordmark {
    position: absolute;
    left: 0;
    right: 0;
    top: 104px;
    display: flex;
    flex-direction: column;
    align-items: center;
  }
  .wordmark__inner {
    display: flex;
    flex-direction: column;
    align-items: flex-end;
  }
  .wordmark__name {
    font-weight: 700;
    font-size: 34px;
    line-height: 1;
    color: var(--ink);
    letter-spacing: 0.2px;
  }
  .wordmark__role {
    font-weight: 400;
    font-size: 16px;
    line-height: 1;
    margin-top: 10px;
    color: var(--ink);
  }
  .contact {
    position: absolute;
    left: 0;
    right: 0;
    top: 118px;
    text-align: center;
    font-weight: 300;
    font-size: 17px;
    line-height: 21px;
    letter-spacing: 0.4px;
  }
</style>
</head>
<body>
  <main class="spread">
    <section class="card card--front">
      <div class="wordmark">
        <div class="wordmark__inner">
          <span class="wordmark__name">Rosalind Parfrey</span>
          <span class="wordmark__role">stylist</span>
        </div>
      </div>
    </section>
    <section class="card card--back">
      <div class="contact">
        <p class="contact__email">rosaparfrey@mailbox-example.co.nz</p>
        <p class="contact__phone">021 846 7193</p>
      </div>
    </section>
  </main>
</body>
</html>
```